Meridale Bed Company Needs Business Card

Looking for a very nice looking business card. Creative but not extravagant. We sell beds and pillows across the U.S. and need something professional but catchy. I have attached the logo.

Name : Devin Holt
Title : President
Phone : (800) 471-2960
Email: sleep@quilmora.com
Website: www.quilmora.com

Can be single-sided or double-sided
horizontal or vertical

Can use Blues/Greys

Target Market(s)

Mass Market

Industry/Entity Type

Retail

Contact Information for Business Card

Name : Devin Holt
Title : President
Phone : (800) 471-2960
Email: sleep@quilmora.com
Website: www.quilmora.com

Requirements
Must have
• Clean, Modern, Smooth
• Can use Blues/Greys
• On the other side without the information - have something simple like www.quilmora.com or our logo
Nice to have
• Surprise me
Should not have
• Nothing crazy, nothing cluttered

```html
<!DOCTYPE html>
<html lang="en">
<head>
<meta charset="utf-8">
<title>Quilmora Business Card</title>
<link rel="stylesheet" href="https://fonts.googleapis.com/css2?family=Montserrat:wght@400;600&family=Quicksand:wght@300;400&display=swap">
<style>
  :root {
    --brand-blue: #34a3d5;
    --brand-blue-soft: #7cc3e4;
    --card-white: #ffffff;
    --backdrop: #eceeef;
  }
  html, body {
    margin: 0;
    padding: 0;
    width: 1200px;
    height: 1200px;
    overflow: hidden;
    background: var(--backdrop);
  }
  .canvas {
    position: relative;
    width: 1200px;
    height: 1200px;
  }
  .card {
    position: absolute;
    width: 780px;
    height: 444px;
    box-sizing: border-box;
  }
  .card-front {
    left: 217px;
    top: 139px;
    background: var(--brand-blue);
    display: flex;
    align-items: center;
    justify-content: center;
  }
  .brand-name {
    font-family: "Quicksand", sans-serif;
    font-weight: 300;
    font-size: 84px;
    letter-spacing: 3px;
    color: var(--card-white);
    margin-top: -20px;
  }
  .card-back {
    left: 211px;
    top: 649px;
    background: var(--card-white);
    border-top: 11px solid var(--brand-blue);
  }
  .person {
    position: absolute;
    left: 0;
    width: 398px;
    top: 166px;
    text-align: center;
    color: var(--brand-blue);
    font-family: "Montserrat", sans-serif;
  }
  .person-name {
    font-size: 44px;
    font-weight: 400;
    margin: 0;
    line-height: 1.1;
  }
  .person-name strong { font-weight: 600; }
  .person-title {
    font-size: 25px;
    font-weight: 400;
    margin: 12px 0 0;
    letter-spacing: 1px;
  }
  .contact-illustration {
    position: absolute;
    left: 379px;
    top: 80px;
    width: 123px;
    height: 306px;
    border-radius: 10px;
    background: linear-gradient(180deg, var(--brand-blue) 0%, var(--brand-blue-soft) 100%);
  }
  .contact-list {
    position: absolute;
    left: 521px;
    top: 0;
    margin: 0;
    padding: 0;
    list-style: none;
    font-family: "Montserrat", sans-serif;
    font-size: 16.5px;
    color: var(--brand-blue);
    line-height: 1.25;
  }
  .contact-list li { position: absolute; white-space: nowrap; }
  .contact-email { top: 106px; }
  .contact-phone { top: 177px; }
  .contact-address { top: 249px; }
  .contact-web { top: 333px; }
</style>
</head>
<body>
<main class="canvas">
  <section class="card card-front">
    <div class="brand-name">quilmora</div>
  </section>

  <section class="card card-back">
    <div class="person">
      <h1 class="person-name">Devin <strong>Holt</strong></h1>
      <p class="person-title">PRESIDENT</p>
    </div>

    <div class="contact-illustration" role="img" aria-label="Stacked contact illustration: envelope, phone handset, house and globe in brand blue"></div>

    <ul class="contact-list">
      <li class="contact-email">sleep@quilmora.com</li>
      <li class="contact-phone">(800) 471-2960</li>
      <li class="contact-address">Your City Address<br>Street Location, NY City, USA</li>
      <li class="contact-web">www.quilmora.com</li>
    </ul>
  </section>
</main>
</body>
</html>
```